I am looking to create a newly designed website for our national leadership conference which is entitled, "The Harbor of Momentum Leadership Summit". The Harbor of Momentum Leadership Summit is a national conference for student leaders that prepares them for career leadership success. The current website can be seen at www.harborofmomentumleadershipsummit.com.

My goal for the new site is to create a more updated, fresh, hip, and exciting look that appeals to the younger generation while also maintaining are professional appeal. The color should be black, white, and gold. We want there to be live videos played and places to insert pictures for the panels as well.

I look forward to seeing you the new creations.

Requirements
Must have
• Ability to play videos on the home page and throughout the website. Also, make sure that the website shows up clearly on an zTablet.
Nice to have
• Nice look

```html
<!DOCTYPE html>
<html lang="en">
<head>
<meta charset="utf-8">
<title>Regional Conferences – Harbor of Momentum</title>
<link href="https://fonts.googleapis.com/css2?family=Roboto:wght@300;400;500;700&display=swap" rel="stylesheet">
<style>
:root{
  --gold:#bb9137;
  --gold-light:#d8b25a;
  --ink:#222;
  --text:#444;
  --muted:#8a8a8a;
  --band:#f3f3f3;
  --nav:#1f1f1f;
  --white:#fff;
}
*{box-sizing:border-box;margin:0;padding:0}
html,body{width:821px;height:1200px;overflow:hidden;background:var(--white);font-family:'Roboto',sans-serif;color:var(--text)}
.page{position:relative;width:821px;height:1200px}
.header{height:85px;position:relative}
.follow{position:absolute;left:51px;top:32px;display:flex;align-items:center;gap:3px;font-size:8px;font-weight:500;color:var(--ink)}
.follow span{margin-right:4px}
.social{width:20px;height:20px;background:#555;display:inline-block}
.brand{position:absolute;left:0;right:0;top:8px;text-align:center}
.brand-mark{width:38px;height:38px;border-radius:50%;background:var(--gold);margin:0 auto 6px}
.brand-name{font-size:12px;font-weight:700;letter-spacing:1.2px;color:var(--ink)}
.register-btn{position:absolute;right:51px;top:24px;width:152px;height:35px;border-radius:18px;background:var(--gold);color:var(--white);font-size:14px;font-weight:500;letter-spacing:.5px;display:flex;align-items:center;justify-content:center}
.nav{height:42px;background:linear-gradient(#2b2b2b,#151515);display:flex;padding-left:58px}
.nav a{color:var(--white);font-size:9.5px;font-weight:500;text-decoration:none;display:flex;align-items:center;padding:0 15.5px}
.nav a.active{background:var(--gold);padding:0 13px}
.crumb{position:absolute;top:150px;left:56px;font-size:8px;color:#666}
.crumb b{color:var(--gold);font-weight:400}
.logo-band{position:absolute;left:0;right:0;background:var(--band);display:flex;align-items:center}
.band-icon{position:absolute;left:52px;width:36px;height:26px;border-radius:50%;background:var(--gold)}
.band-title{position:absolute;left:104px;font-size:15px;font-weight:400;color:var(--ink);line-height:19px;letter-spacing:.3px}
.band-title em{font-style:normal;color:var(--gold)}
.arrow{position:absolute;font-size:20px;color:var(--ink);font-weight:300}
.partners{position:absolute;display:flex;align-items:center;justify-content:space-between}
.partner{font-size:11px;font-weight:700;color:#555;text-align:center;display:flex;align-items:center;gap:4px}
.partner i{width:10px;height:10px;background:var(--gold);display:inline-block}
.badge{width:56px;height:56px;border-radius:50%;background:#9d2a2a}
.section-title{position:absolute;left:0;right:0;display:flex;justify-content:center;align-items:center;gap:10px;font-size:15.5px;color:var(--ink);letter-spacing:.3px}
.section-title i{width:34px;height:24px;border-radius:50%;background:var(--gold)}
.section-title em{font-style:normal;color:var(--gold)}
.intro{position:absolute;left:51px;top:342px;width:406px;font-size:9.6px;line-height:16.4px;color:var(--text)}
.intro p{margin-bottom:6px}
.photo{position:absolute;left:477px;top:345px;width:293px;height:196px;background:linear-gradient(160deg,#d9cdb7 0%,#b99f7c 45%,#5a4638 100%)}
.venues{position:absolute;top:571px;left:0;right:0;height:283px;background:var(--gold);display:flex}
.venue{width:50%;text-align:center;padding-top:28px;color:var(--white)}
.venue-icon{width:77px;height:77px;border-radius:50%;background:var(--white);margin:0 auto 17px;display:flex;align-items:center;justify-content:center}
.venue h3{font-size:12.5px;font-weight:500;margin-bottom:10px}
.venue p{font-size:9.3px;line-height:16px;font-weight:300;width:340px;margin:0 auto 20px;color:#fbf3e2}
.read-more{display:inline-block;width:88px;height:26px;line-height:26px;border-radius:13px;background:var(--ink);font-size:9px;font-weight:500}
.countdown{position:absolute;top:1015px;left:311px;display:flex;gap:25px}
.count{width:51px;height:54px;background:#1b1b1b;border:2px solid #888;border-radius:3px;text-align:center;color:var(--white)}
.count b{display:block;font-size:23px;color:var(--gold-light);font-weight:500;line-height:32px;margin-top:2px}
.count span{font-size:7px}
.footer{position:absolute;left:0;right:0;top:1084px;height:116px;background:#2a2a2a}
.footer-nav{position:absolute;left:51px;top:37px;display:flex;gap:20px}
.footer-nav a{color:var(--white);font-size:8px;font-weight:500;text-decoration:none}
.legal{position:absolute;left:51px;top:68px;font-size:8px;line-height:14.5px;color:#aaa}
.footer-brand{position:absolute;right:50px;top:32px;text-align:center;color:#888}
.footer-brand i{display:block;width:50px;height:40px;border-radius:50%;background:#666;margin:0 auto 8px}
.footer-brand b{font-size:11px;letter-spacing:1px}
</style>
</head>
<body>
<div class="page">
  <header class="header">
    <div class="follow"><span>FOLLOW US</span><i class="social" aria-label="Social link"></i><i class="social"></i><i class="social"></i><i class="social"></i><i class="social"></i></div>
    <div class="brand"><div class="brand-mark"></div><div class="brand-name">HARBOR OF MOMENTUM</div></div>
    <div class="register-btn">REGISTER NOW</div>
  </header>
  <nav class="nav">
    <a>HOME</a><a>ABOUT</a><a>CONFERENCE PROGRAMS</a><a>REGISTER</a><a>SPEAKER PROFILES</a><a class="active">REGIONAL CONFERENCES</a><a>CONTACT</a>
  </nav>
  <div class="crumb">HOME &nbsp;»&nbsp; <b>REGIONAL CONFERENCE</b></div>

  <section class="logo-band" style="top:172px;height:90px">
    <i class="band-icon"></i>
    <div class="band-title">NETWORK WITH<br><em>EXECUTIVES</em></div>
    <span class="arrow" style="left:260px">‹</span>
    <div class="partners" style="left:284px;width:464px">
      <div class="partner"><i></i>Avenview Talent</div>
      <div class="partner">Marlow Futures</div>
      <div class="partner">Brightchord Music</div>
      <div class="partner">Quadrix Systems</div>
      <div class="partner"><i></i>Lantern Burger</div>
    </div>
    <span class="arrow" style="left:760px">›</span>
  </section>

  <h2 class="section-title" style="top:294px"><i></i><span>REGIONAL <em>CONFERENCES</em></span></h2>
  <div class="intro">
    <p>Starting in March 2016, the Harbor of Momentum Leadership Experience will be offering two regional conferences for student leaders who are not able to attend the national conference in Los Angeles, California this November. These two regional conferences are scheduled to take place at Bayou City University-Downtown and Ashford State University</p>
    <p>The two regional conferences are one day professional and leadership development programs that are focused on connecting student leaders with the skills, people, and self-awareness needed to obtain career leadership success in the 21st Century. These power-packed regional conferences provide student leaders with some of the same transformational experiences that occur at the national conference each year.</p>
    <p>Learn more about these powerful regional conferences that will be taking place in 2016!</p>
  </div>
  <div class="photo" role="img" aria-label="Photo of a panel discussion with speakers seated before a student audience"></div>

  <section class="venues">
    <div class="venue">
      <div class="venue-icon"><svg width="34" height="26" viewBox="0 0 34 26"><path d="M17 2 33 9 17 16 1 9Z" fill="#222"/><path d="M8 13v7c5 4 13 4 18 0v-7l-9 4z" fill="#222"/></svg></div>
      <h3>Bayou City University-Downtown</h3>
      <p>Students will learn about more than twenty different leadership skills and qualities that leaders must for a transformational leadership experience that will connect you with an incredible diverse leadership network of students and professionals that provide..</p>
      <span class="read-more">Read More</span>
    </div>
    <div class="venue">
      <div class="venue-icon"><svg width="32" height="26" viewBox="0 0 32 26" fill="#222"><circle cx="16" cy="5" r="3"/><circle cx="6" cy="9" r="2.5"/><circle cx="26" cy="9" r="2.5"/><rect x="12" y="10" width="8" height="12" rx="2"/><rect x="3" y="13" width="6" height="9" rx="2"/><rect x="23" y="13" width="6" height="9" rx="2"/></svg></div>
      <h3>Ashford State University Regional Conference</h3>
      <p>Students will learn about more than twenty different leadership skills and qualities that leaders must for a transformational leadership experience that will connect you with an incredible diverse leadership network of students and professionals that provide..</p>
      <span class="read-more">Read More</span>
    </div>
  </section>

  <section class="logo-band" style="top:854px;height:91px">
    <i class="band-icon"></i>
    <div class="band-title">2015 CONFERENCE<br><em>PARTNERS AND<br>SUPPORTS</em></div>
    <span class="arrow" style="left:260px">‹</span>
    <div class="partners" style="left:284px;width:466px">
      <div class="partner">Westgrid Power</div>
      <div class="partner">Kestrel Motors</div>
      <div class="partner"><i></i>Fernbrew Coffee</div>
      <div class="partner">Saltleaf Grill</div>
      <div class="badge" role="img" aria-label="Partner badge"></div>
    </div>
    <span class="arrow" style="left:760px">›</span>
  </section>

  <h2 class="section-title" style="top:968px"><i></i><span>6TH ANNUAL <em>CONFERENCE COUNTDOWN</em></span></h2>
  <div class="countdown">
    <div class="count"><b>0</b><span>HOURS</span></div>
    <div class="count"><b>0</b><span>MINUTES</span></div>
    <div class="count"><b>0</b><span>SECONDS</span></div>
  </div>

  <footer class="footer">
    <nav class="footer-nav"><a>HOME</a><a>ABOUT</a><a>CONFERENCE</a><a>REGISTER</a><a>TESTIMONIALS</a><a>Y FACTOR</a><a>VIDEOS</a><a>CONTACT</a></nav>
    <div class="legal">Copyright © 2015. Company Name All Right Reserved<br>Privacy Policy &nbsp;|&nbsp; Term &amp; Conditions</div>
    <div class="footer-brand"><i></i><b>HARBOR OF MOMENTUM</b></div>
  </footer>
</div>
</body>
</html>
```